Im want a website LIKE VRX's and FleetHollow.com's with product payment options like Trenzo's

I need a website LIKE VRX with a header made EXACTLY LIKE THAT OF FLEETHOLLOWS .

The front page photo should be like that of FLEETHOLLOW's webpage as well.

The name of the website will be called "M.K. (Caldera Key)".

We will be targeting ALL MARKETS in a small town in central Panama and charging businesses "listing fees" like a phone book does but also providing informational blogs, news, and other interesting activities.

THIS IS A MULTI PAGE WEBSITE

THIS IS WHERE VRX's website meets Brivelle/FleetHollow.

Once the layout is built I will tweak and modify, add information, and upload items for sale.

Here is a list of specific categories that should be listed out above the front page header image/search bar

-- Home -- News -- Travel -- Activities -- Shop & Dine -- Store -- More... --

These categories should be spread across the bottom of the page in three sections:

WHATS SO GREAT ABOUT (Caldera Key),
HAND PICKED TOURS
ACTIVITIES etc.

Also lets use www.Trenzo.example 's
"HOT DESTINATIONS"
"BEAT THE BEST PRICES IN BOQUETE"
"OCTOBERS INSIDER PICKS"
"TOP DESTINATIONS"
and spread them in four sections side-by-side near the bottom of the page.

Overall I would like to see the finished product to be something LIKE VRX's and FleetHollows.

WE NEED ONLINE PAYMENT OPTIONS LIKE BRIVELLE'S WEBSITE HAS

This will be a desktop website but should be very mobile friendly as well.

-rodmund

P.S. Good luck!

If it isn't already too late to change the website name, the name of the website should be "Caldera Key". Added Friday, October 9, 2015

What do you guys think the budget should be to win this? Added Saturday, October 10, 2015

www.palmorra.example is the most amazing simple site. Whoever can make me a replica with my specifications will win immediately!!!! Added Sunday, October 18, 2015

OMG www.palmorra.example is the bomb!So simple and elegant. Whoever can make me an EXACT REPLICA OF WWW.PALMORRA.EXAMPLE as my site with the specifications mentioned in my brief will take home the $825.00 immediately! Good luck amigos! Added Sunday, October 18, 2015

Does anybody know how to add recurring monthly billing options on this website? Added Sunday, October 18, 2015

ALL MARKETS

Product

Coded - Design and coding required

5+ page

• Coinvey payment options.
• I must be able to add and remove photos/text and video from the HTML files in the page.
• Be creative my friends, and may the odds be forever in your favor!
• I added some photos of a good layout for our page below.

```html
<!DOCTYPE html>
<html lang="en">
<head>
<meta charset="utf-8">
<title>Caldera Key</title>
<link href="https://fonts.googleapis.com/css2?family=Open+Sans:wght@400;600;700&family=Raleway:wght@300;400;700&display=swap" rel="stylesheet">
<style>
:root{
  --green:#6cb533;
  --green-dark:#57972a;
  --ink:#333333;
  --muted:#8a8a8a;
  --line:#e3e3e3;
  --panel:#f2f2f2;
  --footer:#262626;
  --footer-deep:#1c1c1c;
  --white:#ffffff;
  --star:#f2b01e;
}
*{box-sizing:border-box;margin:0;padding:0}
html,body{width:688px;height:1200px;overflow:hidden;background:var(--white)}
body{font-family:"Open Sans",Arial,sans-serif;color:var(--ink);font-size:8px;line-height:1.45}
.page{width:688px;height:1200px;position:relative;overflow:hidden}
a{color:inherit;text-decoration:none}

/* top bar */
.topbar{height:18px;display:flex;justify-content:space-between;align-items:center;padding:0 24px;font-size:7px;color:var(--muted);border-bottom:1px solid var(--line)}
.topbar nav{display:flex;gap:8px}
.topbar .right span{margin-left:12px}

/* header */
.header{height:62px;display:flex;align-items:center;justify-content:space-between;padding:0 24px}
.brand{display:flex;align-items:center;gap:8px}
.brand-mark{width:26px;height:26px;border-radius:50%;background:var(--green)}
.brand-name{font-family:"Raleway",sans-serif;font-weight:700;font-size:19px;color:var(--ink);line-height:1}
.main-nav{display:flex;gap:22px;font-size:8px;font-weight:600}
.main-nav a:first-child{color:var(--green)}

/* hero */
.hero{position:relative;height:250px;margin:0 24px;background:linear-gradient(180deg,#9fd2ec 0%,#c8e7f3 40%,#e4d7bc 75%,#d7c39d 100%);overflow:hidden}
.hero-photo{position:absolute;left:0;top:0;width:260px;height:250px;background:linear-gradient(160deg,#e9d4a8 0%,#c69b6a 55%,#8b6a4c 100%);opacity:.55}
.hero-copy{position:absolute;right:40px;top:62px;text-align:right;color:var(--white);font-family:"Raleway",sans-serif}
.hero-copy .line1{font-size:19px;font-weight:300;letter-spacing:1px}
.hero-copy .line2{font-size:26px;font-weight:400;letter-spacing:1px;line-height:1.1}
.search{position:absolute;right:40px;top:138px;display:flex;width:290px;height:24px}
.search span{flex:1;background:var(--white);font-size:7px;color:var(--muted);padding:6px 10px}
.search b{width:60px;background:var(--green);color:var(--white);font-size:7px;display:flex;align-items:center;justify-content:center}
.hero-arrow{position:absolute;top:110px;width:22px;height:22px;border-radius:50%;background:rgba(255,255,255,.6)}
.hero-arrow.left{left:10px}.hero-arrow.right{right:10px}
.hero-dots{position:absolute;bottom:10px;left:50%;transform:translateX(-50%);display:flex;gap:5px}
.hero-dots i{width:6px;height:6px;border-radius:50%;background:rgba(255,255,255,.7)}
.hero-dots i:first-child{background:var(--green)}
.hero-badge{position:absolute;right:60px;top:34px;width:20px;height:20px;border-radius:50%;background:var(--white)}

/* perks */
.perks{height:90px;display:flex;justify-content:space-around;align-items:center;padding:0 40px}
.perk{display:flex;align-items:center;gap:8px}
.perk-icon{width:30px;height:30px;border-radius:50%;background:var(--green);display:flex;align-items:center;justify-content:center}
.perk-title{font-family:"Raleway",sans-serif;font-size:8px;font-weight:700;line-height:1.3;text-transform:uppercase}
.perk-title em{font-style:normal;font-weight:400;display:block}

/* offer cards */
.offers{display:flex;gap:15px;padding:0 44px;height:230px}
.offer{flex:1;position:relative}
.offer-photo{height:115px}
.offer-photo.tours{background:linear-gradient(180deg,#5cb8e6,#8fd3d8 60%,#e5d9b4)}
.offer-photo.hotels{background:linear-gradient(180deg,#7ec6ea,#4fb1c7 55%,#2f8fa6)}
.offer-photo.vehicles{background:linear-gradient(180deg,#c9dde6,#a9b3ad 55%,#6f6a5c)}
.offer-price{position:absolute;top:4px;right:0;background:var(--green);color:var(--white);font-size:7px;font-weight:700;padding:3px 8px}
.offer h3{font-size:8px;font-weight:700;text-transform:uppercase;margin-top:9px}
.stars{color:var(--star);font-size:9px;letter-spacing:1px;line-height:1.4}
.offer p{font-size:6.5px;color:var(--muted);margin-top:2px}
.more{display:inline-block;margin-top:6px;font-size:6.5px;font-weight:700;color:var(--green)}

/* features & destinations */
.info{position:absolute;top:668px;left:0;width:688px;height:222px;background:var(--panel);display:flex;padding:22px 44px;gap:40px}
.section-title{font-size:9px;font-weight:700;text-transform:uppercase;padding-bottom:8px;border-bottom:1px solid #d8d8d8;margin-bottom:14px}
.features{flex:1.2}
.feature-grid{display:grid;grid-template-columns:1fr 1fr;gap:16px 18px}
.feature{display:flex;gap:8px}
.feature-icon{flex:none;width:26px;height:26px;border-radius:4px;background:var(--green)}
.feature h4{font-family:"Raleway",sans-serif;font-size:8px;font-weight:400;color:var(--green);line-height:1.2}
.feature h4 b{display:block;color:var(--ink);font-size:10px}
.feature p{font-size:6.5px;color:var(--muted);margin-top:3px}
.destinations{flex:1}
.dest-list{display:grid;grid-template-columns:1fr 1fr;gap:5px 10px;font-size:6.5px;text-transform:uppercase;color:#555}
.dest-list li{list-style:none;padding-bottom:3px;border-bottom:1px solid #e2e2e2}
.dest-list li::before{content:"›";color:var(--green);margin-right:5px;font-weight:700}

/* contact strip */
.contact{position:absolute;top:892px;left:0;width:688px;height:84px;display:flex;padding:16px 44px;gap:20px}
.contact-item{flex:1}
.contact-item h5{font-size:7px;font-weight:700;color:var(--ink)}
.contact-row{display:flex;align-items:center;gap:5px;margin-top:6px}
.contact-row strong{font-size:12px;font-weight:400;color:var(--green)}
.contact-row .email{font-size:8px;color:var(--ink)}
.contact-item small{display:block;font-size:6px;color:var(--muted)}
.newsletter{display:flex;margin-top:6px;height:18px}
.newsletter span{flex:1;border:1px solid var(--line);font-size:6px;color:var(--muted);padding:3px 6px}
.newsletter b{width:22px;background:var(--green)}

/* footer */
.footer{position:absolute;top:976px;left:0;width:688px;height:224px;background:var(--footer);color:#bdbdbd}
.footer-inner{display:flex;padding:20px 44px 0;gap:30px;height:198px}
.footer-brand{flex:1.4}
.footer-brand .brand-name{color:var(--white);font-size:22px}
.footer-brand p{font-size:6.5px;margin-top:12px;line-height:1.6}
.footer-brand .more{margin-top:4px}
.footer-col{flex:1}
.footer-col h6{font-size:7.5px;font-weight:700;color:var(--green);text-transform:uppercase;margin-bottom:10px}
.footer-col li{list-style:none;font-size:6.5px;margin-bottom:6px}
.social li{display:flex;align-items:center;gap:6px}
.social li i{width:10px;height:10px;border-radius:50%;background:var(--green);display:inline-block}
.copyright{height:26px;background:var(--footer-deep);font-size:6.5px;display:flex;align-items:center;justify-content:flex-end;padding:0 44px}
</style>
</head>
<body>
<div class="page">

  <div class="topbar">
    <nav><a>Blog</a><a>Leave Feedback</a><a>FAQ</a><a>Contact</a></nav>
    <div class="right"><span>USD ▾</span><span>English ▾</span><span>Login</span><span>Register</span></div>
  </div>

  <header class="header">
    <div class="brand"><span class="brand-mark"></span><span class="brand-name">Caldera Key</span></div>
    <nav class="main-nav"><a>Home</a><a>About Us</a><a>Tours</a><a>Hotels</a><a>Rental Vehicles</a><a>Contact</a></nav>
  </header>

  <section class="hero" role="img" aria-label="Woman in a sun hat relaxing on a tropical beach by turquoise water">
    <div class="hero-photo"></div>
    <div class="hero-badge"></div>
    <div class="hero-copy">
      <div class="line1">CHANGE YOUR LOCATION</div>
      <div class="line2">IT MAY CHANGE YOURSELF</div>
    </div>
    <div class="search"><span>Where do you want to go?</span><b>SEARCH</b></div>
    <span class="hero-arrow left"></span><span class="hero-arrow right"></span>
    <div class="hero-dots"><i></i><i></i><i></i><i></i></div>
  </section>

  <section class="perks">
    <div class="perk">
      <span class="perk-icon"><svg width="14" height="14" viewBox="0 0 14 14"><path d="M2 7l3 3 7-7" stroke="#fff" stroke-width="2" fill="none"/></svg></span>
      <div class="perk-title">Handpicked<em>Tours &amp; Activities</em></div>
    </div>
    <div class="perk">
      <span class="perk-icon"><svg width="14" height="14" viewBox="0 0 14 14"><path d="M7 1l1.8 3.9 4.2.4-3.2 2.8 1 4.2L7 10.1 3.2 12.3l1-4.2L1 5.3l4.2-.4z" fill="#fff"/></svg></span>
      <div class="perk-title">VIP<em>Access</em></div>
    </div>
    <div class="perk">
      <span class="perk-icon"><svg width="14" height="14" viewBox="0 0 14 14"><path d="M3 1h3l1 3-2 1.5a8 8 0 0 0 3.5 3.5L10 7l3 1v3a2 2 0 0 1-2 2A10 10 0 0 1 1 3a2 2 0 0 1 2-2z" fill="#fff"/></svg></span>
      <div class="perk-title">24/7 Support<em>With a Live Person</em></div>
    </div>
  </section>

  <section class="offers">
    <article class="offer">
      <div class="offer-photo tours" role="img" aria-label="Palm trees over a sunny beach"></div>
      <span class="offer-price">Just $25</span>
      <h3>Selling Guided Tours</h3>
      <div class="stars">★★★★★</div>
      <p>Lorem ipsum dolor sit amet, consectetur adipiscing elit. Quisque dignissim ac ipsum vel tempus. Donec pretium.</p>
      <a class="more">READ MORE ›</a>
    </article>
    <article class="offer">
      <div class="offer-photo hotels" role="img" aria-label="Overwater bungalows on a lagoon"></div>
      <span class="offer-price">Just $34</span>
      <h3>Panama Hotel/Hostels</h3>
      <div class="stars">★★★★★</div>
      <p>Lorem ipsum dolor sit amet, consectetur adipiscing elit. Quisque dignissim ac ipsum vel tempus. Donec pretium.</p>
      <a class="more">READ MORE ›</a>
    </article>
    <article class="offer">
      <div class="offer-photo vehicles" role="img" aria-label="Rider on a rental scooter on a town street"></div>
      <span class="offer-price">Just $15</span>
      <h3>Panama Rental Vehicles</h3>
      <div class="stars">★★★★★</div>
      <p>Lorem ipsum dolor sit amet, consectetur adipiscing elit. Quisque dignissim ac ipsum vel tempus. Donec pretium.</p>
      <a class="more">READ MORE ›</a>
    </article>
  </section>

  <section class="info">
    <div class="features">
      <h2 class="section-title">Features</h2>
      <div class="feature-grid">
        <div class="feature"><span class="feature-icon"></span><div><h4>Special<b>Activities</b></h4><p>Lorem ipsum dolor sit amet, consectetur adipiscing elit. Quisque dignissim ac ipsum sit amet.</p></div></div>
        <div class="feature"><span class="feature-icon"></span><div><h4>Travel<b>Arrangements</b></h4><p>Lorem ipsum dolor sit amet, consectetur adipiscing elit. Quisque dignissim ac ipsum sit amet.</p></div></div>
        <div class="feature"><span class="feature-icon"></span><div><h4>Private<b>Guide</b></h4><p>Lorem ipsum dolor sit amet, consectetur adipiscing elit. Quisque dignissim ac ipsum sit amet.</p></div></div>
        <div class="feature"><span class="feature-icon"></span><div><h4>Location<b>Manager</b></h4><p>Lorem ipsum dolor sit amet, consectetur adipiscing elit. Quisque dignissim ac ipsum sit amet.</p></div></div>
      </div>
    </div>
    <div class="destinations">
      <h2 class="section-title">Hot Destinations</h2>
      <ul class="dest-list">
        <li>Las Vegas</li><li>Venice</li>
        <li>Rome</li><li>Milan</li>
        <li>New York City</li><li>San Francisco</li>
        <li>London</li><li>Tokyo</li>
        <li>Amsterdam</li><li>Melbourne</li>
        <li>Barcelona</li><li>Berlin</li>
        <li>Florence</li><li>Paris</li>
      </ul>
    </div>
  </section>

  <section class="contact">
    <div class="contact-item">
      <h5>Book by Phone</h5>
      <div class="contact-row"><svg width="10" height="10" viewBox="0 0 14 14"><path d="M3 1h3l1 3-2 1.5a8 8 0 0 0 3.5 3.5L10 7l3 1v3a2 2 0 0 1-2 2A10 10 0 0 1 1 3a2 2 0 0 1 2-2z" fill="#6cb533"/></svg><strong>1-555-014-2290</strong></div>
      <small>Booking hours 8am - 9pm</small>
    </div>
    <div class="contact-item">
      <h5>Services and Support</h5>
      <div class="contact-row"><svg width="10" height="8" viewBox="0 0 14 10"><rect x=".5" y=".5" width="13" height="9" fill="none" stroke="#6cb533"/><path d="M.5.5l6.5 5 6.5-5" fill="none" stroke="#6cb533"/></svg><span class="email">support@calderakey.example</span></div>
      <small>24-hour online help</small>
    </div>
    <div class="contact-item">
      <h5>Brilliant causes to book</h5>
      <div class="contact-row"><svg width="10" height="10" viewBox="0 0 14 14"><path d="M2 7l3 3 7-7" stroke="#6cb533" stroke-width="2" fill="none"/></svg><span class="email">Mileage program</span></div>
      <small>Earn frequent flyer miles</small>
    </div>
    <div class="contact-item">
      <h5>Deals &amp; Discounts</h5>
      <div class="newsletter"><span>Enter your email address</span><b></b></div>
    </div>
  </section>

  <footer class="footer">
    <div class="footer-inner">
      <div class="footer-brand">
        <div class="brand"><span class="brand-mark"></span><span class="brand-name">Caldera Key</span></div>
        <p>Lorem ipsum dolor sit amet, consectetur adipiscing elit. Quisque dignissim ac ipsum vel tempus. Nullam gravida diam non.</p>
        <a class="more">Read More ›</a>
      </div>
      <div class="footer-col">
        <h6>Company</h6>
        <ul><li>About Us</li><li>Press Center</li><li>Careers</li><li>Site Map</li><li>Free Newsletter</li></ul>
      </div>
      <div class="footer-col">
        <h6>Support</h6>
        <ul><li>Customer Care</li><li>Privacy Policy</li><li>Low Price Guarantee</li><li>Group Services</li><li>Mileage Program</li></ul>
      </div>
      <div class="footer-col">
        <h6>Stay in Touch</h6>
        <ul class="social"><li><i></i>Facetome</li><li><i></i>Chirper</li><li><i></i>Circleo</li><li><i></i>Snapgram</li></ul>
      </div>
    </div>
    <div class="copyright">Caldera Key © 2015 · All rights reserved</div>
  </footer>

</div>
</body>
</html>
```